Tolvar Air and Electrical Website

Simple and easy to use website for a Electrical and Air Conditioning contracting business.Use stock photosOnline contact portallogo still to be supplied

Target Market(s)

Mums and Dads who want a local contractor

Coding

Coded - Design and coding required

Number of Pages Required

2 page

Font styles to use
Sans Serif

Colors
f04a50
3276b5
33a6d7

Requirements
Must have
• Simple and easy to use
• Ph number
• 4 web address; linked to page
• 0417385926
• tolvar.com.au
• tolvarelectrical.com.au
• tolvarairandelectrical.com.au
• tolvarair.com.au
Nice to have
• Split System Air Con Picture
• Electrical Pictures

```html
<!DOCTYPE html>
<html lang="en">
<head>
<meta charset="utf-8">
<title>Tolvar Air and Electrical</title>
<link rel="stylesheet" href="https://fonts.googleapis.com/css2?family=Josefin+Sans:wght@300;400&family=Lato:wght@400;700&display=swap">
<style>
:root{
  --red:#f04a50;
  --blue:#3276b5;
  --sky:#33a6d7;
  --ink:#222;
  --muted:#666;
  --light:#f4f4f4;
  --white:#fff;
}
*{box-sizing:border-box;margin:0;padding:0}
html,body{width:1200px;height:3735px;overflow:hidden}
body{font-family:'Lato',sans-serif;color:var(--ink);background:var(--white);position:relative}
.abs{position:absolute}
.display{font-family:'Josefin Sans',sans-serif;font-weight:300}

/* header */
.site-header{position:absolute;left:0;top:0;width:1200px;height:113px;background:var(--white)}
.brand{position:absolute;left:113px;top:34px;display:flex;align-items:center;gap:14px;font-family:'Josefin Sans',sans-serif;font-weight:400;font-size:36px;color:#333}
.brand-dot{width:40px;height:40px;border-radius:50%;background:var(--blue)}
.main-nav{position:absolute;top:50px;font-size:14.5px;color:#333}
.main-nav a{position:absolute;white-space:nowrap;color:inherit;text-decoration:none}
.main-nav a.active{color:var(--red)}

/* hero */
.hero{position:absolute;left:0;top:113px;width:1200px;height:648px;background:linear-gradient(120deg,#3b4250 0%,#8a8f96 40%,#c9c4b8 60%,#5a5f68 100%)}
.hero-card{position:absolute;left:112px;top:181px;width:477px;height:304px;background:linear-gradient(110deg,rgba(240,74,80,.82) 0%,rgba(150,80,170,.78) 55%,rgba(70,100,210,.75) 100%);color:var(--white);padding:0 42px}
.hero-title{font-size:56px;margin-top:30px;line-height:1}
.hero-text{font-size:16px;line-height:33px;margin-top:22px}
.btn-ghost{display:inline-block;margin-top:20px;width:143px;height:50px;border:1.5px solid var(--white);border-radius:25px;text-align:center;line-height:47px;font-size:16px;color:var(--white)}

/* welcome */
.welcome-photo{position:absolute;left:152px;top:853px;width:491px;height:395px;background:linear-gradient(135deg,#d8dee4 0%,#4f8fcf 45%,#c7b5a2 100%)}
.welcome-body{position:absolute;left:688px;top:874px;width:372px}
.welcome-kicker{font-family:'Josefin Sans',sans-serif;font-size:19px;font-weight:400;color:#222}
.welcome-sub{font-size:26px;line-height:33px;color:#777;margin-top:24px}
.welcome-text{font-size:13px;line-height:29px;color:#555;margin-top:26px;text-align:justify}
.btn-solid{position:absolute;left:0;top:308px;width:141px;height:47px;background:var(--blue);color:var(--white);font-size:17px;line-height:47px;text-align:center}

/* section heads */
.section-title{position:absolute;left:0;width:1200px;text-align:center;font-size:41px;color:#333}
.title-rule{position:absolute;left:575px;width:50px;height:2px;background:var(--red)}

/* services */
.services{position:absolute;left:0;top:1345px;width:1200px;height:708px;background:var(--light)}
.service-card{position:absolute;top:152px;width:306px;height:490px;background:var(--white);box-shadow:0 1px 3px rgba(0,0,0,.08);text-align:center}
.service-photo{width:100%;height:236px}
.service-name{font-size:27px;color:#333;margin-top:32px}
.service-text{font-size:12px;line-height:25.5px;color:#555;margin:22px auto 0;width:264px}
.btn-outline{display:inline-block;margin-top:23px;width:116px;height:41px;border:1px solid var(--red);border-radius:21px;color:var(--red);font-size:12.5px;line-height:39px}

/* call band */
.call-band{position:absolute;left:0;top:2053px;width:1200px;height:397px;background:linear-gradient(100deg,#2c2a2e 0%,#4a4544 45%,#3a3537 70%,#232226 100%);text-align:center;color:var(--white)}
.call-head{position:absolute;left:0;width:1200px;top:118px;font-family:'Josefin Sans',sans-serif;font-weight:400;font-size:38px;letter-spacing:.5px}
.call-sub{position:absolute;left:0;width:1200px;top:167px;font-size:27px}
.call-btn{position:absolute;left:446px;top:236px;width:306px;height:66px;border-radius:33px;background:var(--red);display:flex;align-items:center}
.call-icon{width:54px;height:54px;margin-left:8px;border-radius:50%;background:var(--white);display:flex;align-items:center;justify-content:center}
.call-num{font-family:'Josefin Sans',sans-serif;font-weight:400;font-size:23px;margin-left:24px;margin-top:4px}

/* news */
.news-card{position:absolute;top:2588px;width:306px;height:409px;background:var(--white);box-shadow:0 1px 4px rgba(0,0,0,.12)}
.news-photo{width:100%;height:236px}
.news-meta{font-family:'Josefin Sans',sans-serif;font-size:12.5px;color:#555;margin:26px 0 0 20px}
.news-title{font-family:'Josefin Sans',sans-serif;font-weight:400;font-size:21px;color:#333;margin:18px 0 0 20px}
.news-text{font-size:13px;line-height:23px;color:#666;margin:10px 20px 0}

/* testimonials */
.testimonials{position:absolute;left:0;top:3065px;width:1200px;height:347px;background:#f7f7f7}
.quote{position:absolute;left:225px;top:128px;width:750px;text-align:center;font-size:14px;line-height:33.5px;color:#555}
.quote-mark{font-family:Georgia,serif;font-size:22px;font-weight:700;color:#333;line-height:0}
.quote-name{position:absolute;left:0;width:1200px;top:252px;text-align:center;font-family:'Josefin Sans',sans-serif;font-weight:400;font-size:22px;color:var(--red)}

/* footer */
.site-footer{position:absolute;left:0;top:3412px;width:1200px;height:323px;background:var(--red);color:var(--white);text-align:center}
.footer-brand{position:absolute;left:0;width:1200px;top:42px;font-size:70px}
.footer-nav{position:absolute;left:0;width:1200px;top:138px;font-size:14px}
.footer-nav span.sep{margin:0 22px}
.socials{position:absolute;left:497px;top:189px;display:flex;gap:8px}
.socials span{width:35px;height:35px;border:1.5px solid var(--white);border-radius:50%}
.copyright{position:absolute;left:0;width:1200px;top:262px;font-size:13px}
</style>
</head>
<body>

<header class="site-header">
  <div class="brand"><span class="brand-dot"></span>Tolvar</div>
  <nav class="main-nav">
    <a class="active" style="left:485px">Home</a>
    <a style="left:581px">About Us</a>
    <a style="left:698px">Services</a>
    <a style="left:810px">Product</a>
    <a style="left:918px">News</a>
    <a style="left:1011px">Contact Us</a>
  </nav>
</header>

<section class="hero" role="img" aria-label="Photo of hands testing a switchboard with a multimeter">
  <div class="hero-card">
    <h1 class="hero-title display">Tolvar</h1>
    <p class="hero-text">Sed ut perspiciatis unde omnis iste natus error sit vol uptatem accusantium doloremque laudantium, tota beatae vitae dicta sunt explicabo.</p>
    <span class="btn-ghost">Read More</span>
  </div>
</section>

<div class="welcome-photo" role="img" aria-label="Photo of a technician servicing a split system air conditioner"></div>
<div class="welcome-body">
  <h2 class="welcome-kicker">Welcome to Tolvar</h2>
  <p class="welcome-sub display">Electrical &amp; Air Conditioning<br>contracting business</p>
  <p class="welcome-text">Sed ut perspiciatis unde omnis iste natus error sit voluptatem accusantium doloremque laudantium, totam rem aperiam, eaque ipsa quae ab illo inventore veritatis et quasi architecto beatae vitae dicta sunt explicabo. Nemo enim ipsam volupta quia qui ratione voluptatem sequi nesciunt</p>
  <span class="btn-solid">Read More</span>
</div>

<section class="services">
  <h2 class="section-title display" style="top:42px">Our Services</h2>
  <div class="title-rule" style="top:97px"></div>

  <article class="service-card" style="left:112px">
    <div class="service-photo" role="img" aria-label="Photo of a technician cleaning an air conditioner unit" style="background:linear-gradient(135deg,#e9ecef,#b9c3cc 60%,#3e4c66)"></div>
    <h3 class="service-name display">Air Conditioning</h3>
    <p class="service-text">Sed ut perspiciatis unde omnis iste natus error sit voluptatem accusantium doloremque lau-dantium, totam rem aperiam,</p>
    <span class="btn-outline">Read More</span>
  </article>

  <article class="service-card" style="left:446px">
    <div class="service-photo" role="img" aria-label="Photo of coloured electrical cables" style="background:linear-gradient(135deg,#1d3a6b,#3f7fc4 50%,#a94a4a)"></div>
    <h3 class="service-name display">Electrical</h3>
    <p class="service-text">Sed ut perspiciatis unde omnis iste natus error sit voluptatem accusantium doloremque lau-dantium, totam rem aperiam,</p>
    <span class="btn-outline">Read More</span>
  </article>

  <article class="service-card" style="left:781px">
    <div class="service-photo" role="img" aria-label="Photo of a client signing a contract" style="background:linear-gradient(135deg,#c9d3dc,#7f93b0 55%,#34476a)"></div>
    <h3 class="service-name display">Contracting Business</h3>
    <p class="service-text">Sed ut perspiciatis unde omnis iste natus error sit voluptatem accusantium doloremque lau-dantium, totam rem aperiam,</p>
    <span class="btn-outline">Read More</span>
  </article>
</section>

<section class="call-band" role="img" aria-label="Darkened photo of an electrician at a switchboard">
  <p class="call-head">Sed ut perspiciatis unde omnis iste natus error</p>
  <p class="call-sub display">sit voluptatem accusantium doloremque</p>
  <div class="call-btn">
    <span class="call-icon">
      <svg width="18" height="18" viewBox="0 0 24 24"><path fill="#f04a50" d="M6.6 10.8a15.1 15.1 0 0 0 6.6 6.6l2.2-2.2a1 1 0 0 1 1-.25 11.4 11.4 0 0 0 3.6.57 1 1 0 0 1 1 1V20a1 1 0 0 1-1 1A17 17 0 0 1 3 4a1 1 0 0 1 1-1h3.5a1 1 0 0 1 1 1c0 1.25.2 2.45.57 3.57a1 1 0 0 1-.25 1z"/></svg>
    </span>
    <span class="call-num">Call : 0417385926</span>
  </div>
</section>

<h2 class="section-title display" style="top:2494px">Latest News</h2>
<div class="title-rule" style="top:2547px"></div>

<article class="news-card" style="left:112px">
  <div class="news-photo" role="img" aria-label="Photo of a multimeter testing wiring" style="background:linear-gradient(135deg,#8a5a7a,#c9a06a 50%,#2d3f8a)"></div>
  <p class="news-meta">By Admin / 06 June 2019</p>
  <h3 class="news-title">Sed ut perspiciatis unde</h3>
  <p class="news-text">Sed ut perspiciatis unde omnis iste natus error sit voluptatem accusantium</p>
</article>
<article class="news-card" style="left:446px">
  <div class="news-photo" role="img" aria-label="Photo of a technician repairing an outdoor air conditioning unit" style="background:linear-gradient(135deg,#c6ccd4,#6d7a8e 55%,#2b3550)"></div>
  <p class="news-meta">By Admin / 06 June 2019</p>
  <h3 class="news-title">Sed ut perspiciatis unde</h3>
  <p class="news-text">Sed ut perspiciatis unde omnis iste natus error sit voluptatem accusantium</p>
</article>
<article class="news-card" style="left:781px">
  <div class="news-photo" role="img" aria-label="Photo of outdoor condenser units beside a house" style="background:linear-gradient(160deg,#d9d0bf,#a9aaa6 55%,#5f8a3c)"></div>
  <p class="news-meta">By Admin / 06 June 2019</p>
  <h3 class="news-title">Sed ut perspiciatis unde</h3>
  <p class="news-text">Sed ut perspiciatis unde omnis iste natus error sit voluptatem accusantium</p>
</article>

<section class="testimonials">
  <h2 class="section-title display" style="top:42px">Our Testimonials</h2>
  <div class="title-rule" style="top:97px"></div>
  <p class="quote"><span class="quote-mark">&ldquo;</span> Sed ut perspiciatis unde omnis iste natus error sit voluptatem accusantium doloremque laudantium, totam rem aperiam, eaque ipsa quae ab illo inventore veritatis et quasi architecto beatae vitae dicta sunt explicabo. quia consequuntur magni dolores eos qui ratione voluptatem sequi nesciunt. <span class="quote-mark">&rdquo;</span></p>
  <p class="quote-name">-Mara Lindqvist</p>
</section>

<footer class="site-footer">
  <p class="footer-brand display">Tolvar</p>
  <nav class="footer-nav">Home<span class="sep">/</span>About Us<span class="sep">/</span>Services<span class="sep">/</span>Product<span class="sep">/</span>News<span class="sep">/</span>Contact Us</nav>
  <div class="socials" aria-label="Social links"><span></span><span></span><span></span><span></span><span></span></div>
  <p class="copyright">© Copyright 2019 Tolvar.All Rights Reserved</p>
</footer>

</body>
</html>
```